SkyvornQ Business Cards and Stationary Design

Need a design for our business cards and stationary. I want to carry on the theme of the logo. I want the business cards to have a design on the back. I would like the business cards and the stationary to carry the same theme, design scheme, and branding

Target Market(s)

Airlines and Maintenance Facilities

Industry/Entity Type

Aviation

Contact Information for Business Card

Name
Position Title
Address: 4827 Trellis Hollow Road, Marlowe Bay, Westhaven, 34951
Office Number
Mobile Number
Email
Website

Font styles to use
Serif
Sans Serif

Colors

Designer to choose colors to be used in the design.

```html
<!DOCTYPE html>
<html lang="en">
<head>
<meta charset="utf-8">
<title>SkyvornQ Business Card</title>
<link href="https://fonts.googleapis.com/css2?family=Roboto:wght@400;500;700&display=swap" rel="stylesheet">
<style>
  :root {
    --page: #e9ebee;
    --card: #ffffff;
    --navy: #0b2a5a;
    --navy-deep: #071d42;
    --blue: #1f63b6;
    --sky: #2fa3e6;
    --text-light: #ffffff;
    --shadow: rgba(10, 25, 50, 0.18);
  }
  * { margin: 0; padding: 0; box-sizing: border-box; }
  html, body { width: 1200px; height: 911px; overflow: hidden; }
  body {
    background: var(--page);
    font-family: "Roboto", Arial, sans-serif;
    position: relative;
  }
  .card {
    position: absolute;
    top: 123px;
    width: 380px;
    height: 665px;
    background: var(--card);
    border-radius: 22px;
    overflow: hidden;
    box-shadow: 0 10px 30px var(--shadow);
  }
  .card--front { left: 190px; }
  .card--back { left: 630px; }

  .card__shape { position: absolute; inset: 0; }

  .wordmark {
    display: flex;
    align-items: center;
    gap: 12px;
    color: var(--navy);
    font-weight: 700;
    letter-spacing: 5px;
    text-transform: uppercase;
  }
  .wordmark__dot {
    border: 4px solid var(--blue);
    border-radius: 50%;
    flex: none;
  }
  .card--front .wordmark {
    position: absolute;
    top: 70px;
    left: 0; right: 0;
    justify-content: center;
    font-size: 26px;
  }
  .card--front .wordmark__dot { width: 30px; height: 30px; }

  .contact {
    position: absolute;
    left: 32px;
    top: 330px;
    color: var(--text-light);
  }
  .contact__name {
    font-size: 22px;
    font-weight: 500;
    color: var(--sky);
    text-transform: uppercase;
    letter-spacing: 1px;
  }
  .contact__title {
    font-size: 15px;
    text-transform: uppercase;
    margin-top: 2px;
  }
  .contact__address {
    font-size: 14px;
    line-height: 1.45;
    margin-top: 34px;
    width: 240px;
  }
  .contact__list {
    list-style: none;
    margin-top: 18px;
    font-size: 14px;
    line-height: 1.6;
  }
  .contact__list li { display: flex; align-items: center; gap: 10px; }
  .contact__icon { width: 13px; height: 13px; flex: none; fill: var(--sky); }

  .card--back .wordmark {
    position: absolute;
    top: 270px;
    left: 0; right: 0;
    justify-content: center;
    font-size: 30px;
  }
  .card--back .wordmark__dot { width: 40px; height: 40px; }

  .web-band {
    position: absolute;
    left: 0; right: 0;
    top: 545px;
    height: 38px;
    background: linear-gradient(90deg, var(--navy-deep), var(--blue) 55%, var(--navy));
    color: var(--text-light);
    font-size: 14px;
    letter-spacing: 6px;
    display: flex;
    align-items: center;
    justify-content: center;
  }
</style>
</head>
<body>

<section class="card card--front" aria-label="Business card front">
  <svg class="card__shape" viewBox="0 0 380 665" preserveAspectRatio="none" aria-hidden="true">
    <defs>
      <linearGradient id="sweep" x1="0" y1="0" x2="1" y2="1">
        <stop offset="0" stop-color="#2fa3e6"/>
        <stop offset="1" stop-color="#1a4f9c"/>
      </linearGradient>
      <linearGradient id="panel" x1="0" y1="0" x2="0" y2="1">
        <stop offset="0" stop-color="#0b2a5a"/>
        <stop offset="1" stop-color="#071d42"/>
      </linearGradient>
    </defs>
    <path d="M0,190 C195,190 335,390 372,665 L0,665 Z" fill="url(#sweep)"/>
    <path d="M0,205 C180,212 305,400 335,665 L0,665 Z" fill="url(#panel)"/>
  </svg>

  <div class="wordmark">
    <span class="wordmark__dot"></span>
    <span>SkyvornQ</span>
  </div>

  <div class="contact">
    <p class="contact__name">Dorian Kell</p>
    <p class="contact__title">CEO/Founder</p>
    <p class="contact__address">4827 Trellis Hollow Road<br>Marlowe Bay, Westhaven, 34951</p>
    <ul class="contact__list">
      <li>
        <svg class="contact__icon" viewBox="0 0 16 16"><path d="M3 1h3l1.5 4-2 1.3a9 9 0 0 0 4.2 4.2l1.3-2 4 1.5v3a1.5 1.5 0 0 1-1.5 1.5A13.5 13.5 0 0 1 1.5 2.5 1.5 1.5 0 0 1 3 1z"/></svg>
        772 510 4186
      </li>
      <li>
        <svg class="contact__icon" viewBox="0 0 16 16"><path d="M4 0h8a1 1 0 0 1 1 1v14a1 1 0 0 1-1 1H4a1 1 0 0 1-1-1V1a1 1 0 0 1 1-1zm1 2v10h6V2zm3 11a1 1 0 1 0 0 2 1 1 0 0 0 0-2z"/></svg>
        772 903 2657
      </li>
      <li>
        <svg class="contact__icon" viewBox="0 0 16 16"><path d="M1 3h14v10H1zm1.5 1.5L8 9l5.5-4.5z"/></svg>
        info@skyvornq.com
      </li>
      <li>
        <svg class="contact__icon" viewBox="0 0 16 16"><circle cx="8" cy="8" r="7"/></svg>
        www.skyvornq.com
      </li>
    </ul>
  </div>
</section>

<section class="card card--back" aria-label="Business card back">
  <div class="wordmark">
    <span class="wordmark__dot"></span>
    <span>SkyvornQ</span>
  </div>
  <div class="web-band">www.skyvornq.com</div>
</section>

</body>
</html>
```